Sophisticated, clean website reflecting my feminine, playful side to sell my abstract art,

I need a website no more than 3 pages to showcase my paintings, a little about me and some contact info. I do abstracts so looking for something a little edgy, yet feminine and current.
Updates

Hi there, These are some artists websites that I Iike: Marnelvoss.com (I like how airy it is) peterwallombry.com garethpolvens.com (I like how it scrolls) I'll need a place for a photo ( a headshot-i do not have it yet so I'll need to be able to upload that later) as well as an area for my bio. Also, it's important that I will be able to upload any new photos and descriptions easily so it should be user friendly. Lastly, I like in a sunny place so would like to have this seem upbeat and playful as that is how i like to paint. thanks-I'm trying to upload my photos now -

Target Market(s)

ppl ages 35-70 who want large scale art for their homes

Industry/Entity Type

art

Coding

Coded - Design and coding required

Number of Pages Required

3 page

Colors

Designer to choose colors to be used in the design.

Requirements
Must have
• photos of my art, a place for my bio, be easy to reach me. tasteful-nothing too "in your face" -my clients are pretty high end and organized. They like clean lines
Nice to have
• sophisticated background, muted tones in the back-similar clean font throughout-no cursive
Should not have
• too many dark areas. Too many blocks of color. Too serious.

```html
<!DOCTYPE html>
<html lang="en">
<head>
<meta charset="utf-8">
<title>Lena Marlowe — Abstract Paintings</title>
<link rel="stylesheet" href="https://fonts.googleapis.com/css2?family=Rubik+Dirt&family=Barlow+Condensed:wght@600&family=Barlow:wght@300;400;600&display=swap">
<style>
:root{
  --ink:#111111;
  --text:#333333;
  --muted:#6b6b6b;
  --gold:#b3a67c;
  --gold-soft:#c4b99a;
  --sand:#cdc4b7;
  --cream:#f9f6f0;
  --footer:#f2f2f2;
  --rule:#d6d6d6;
  --white:#ffffff;
}
*{margin:0;padding:0;box-sizing:border-box}
html,body{width:1200px;height:2932px;overflow:hidden;background:var(--white)}
body{position:relative;font-family:"Barlow",sans-serif;color:var(--text)}
.abs{position:absolute}
.display{font-family:"Rubik Dirt",sans-serif;color:var(--ink);letter-spacing:1px;line-height:1}
.nav-font{font-family:"Barlow Condensed",sans-serif;font-weight:600;color:var(--ink);text-transform:uppercase}

/* header */
.site-header{left:0;top:0;width:1200px;height:100px;border-bottom:2px solid var(--rule)}
.brand{display:flex;align-items:center;gap:16px}
.brand-mark{width:50px;height:50px;background:var(--ink)}
.header-brand{left:333px;top:26px}
.header-brand .display{font-size:50px}
.main-nav{top:100px;left:0;width:1200px;height:65px}
.main-nav a{position:absolute;top:20px;font-size:22px;text-decoration:none}
.main-nav .active{border-bottom:3px solid var(--ink);padding-bottom:4px}
.social-dot{border-radius:50%;background:var(--ink)}

/* hero */
.hero{left:0;top:165px;width:1200px;height:628px;
  background:
   radial-gradient(ellipse 420px 300px at 330px 200px,#3f9a3c 0%,rgba(63,154,60,0) 100%),
   radial-gradient(ellipse 360px 260px at 650px 300px,#1f7a6d 0%,rgba(31,122,109,0) 100%),
   radial-gradient(ellipse 380px 280px at 980px 480px,#6b4b2c 0%,rgba(107,75,44,0) 100%),
   radial-gradient(ellipse 300px 220px at 1000px 140px,#b8b070 0%,rgba(184,176,112,0) 100%),
   linear-gradient(120deg,#d9dbd6 0%,#6fae4a 30%,#2f7f62 55%,#7e6a45 80%,#5a3e26 100%)}
.hero-arrow{top:260px;width:64px;height:74px;background:rgba(60,60,60,.75)}
.hero-title{left:0;width:1200px;text-align:center;color:var(--white)}
.hero-dots{top:586px;left:544px;display:flex;gap:9px}
.hero-dots span{width:12px;height:12px;border-radius:50%;background:var(--white)}
.hero-dots span:first-child{background:transparent;border:2px solid var(--white)}

/* about */
.portrait-frame{left:150px;top:952px;width:373px;height:381px;border-right:6px solid var(--sand);border-bottom:6px solid var(--sand)}
.portrait{left:115px;top:930px;width:393px;height:386px;background:radial-gradient(circle at 50% 45%,#e6e2de 0%,#f2f2f2 60%,#f6f6f6 100%)}
.section-heading{font-size:52px}
.underline{height:3px;background:var(--gold)}
.about-copy{left:603px;top:1030px;width:475px;font-size:16px;font-weight:300;line-height:27px;color:var(--text)}
.about-copy p+p{margin-top:14px;text-align:justify}
.btn-outline{left:603px;top:1267px;width:180px;height:49px;border:2px solid var(--ink);display:flex;align-items:center;justify-content:center;font-size:18px;color:var(--gold);letter-spacing:.5px}

/* gallery */
.gallery{left:0;top:1439px;width:1200px;height:816px;background:var(--cream)}
.gallery-title{left:0;top:69px;width:1200px;text-align:center;font-size:46px}
.gallery-artwork{left:117px;top:168px;width:950px;height:559px;
  background:
   radial-gradient(ellipse 220px 180px at 250px 200px,#5a2a22 0%,rgba(90,42,34,0) 100%),
   radial-gradient(ellipse 240px 200px at 760px 180px,#d8a2a0 0%,rgba(216,162,160,0) 100%),
   radial-gradient(ellipse 200px 160px at 700px 480px,#7a3b2e 0%,rgba(122,59,46,0) 100%),
   linear-gradient(120deg,#e8e2dc 0%,#b88070 40%,#e6c6c0 65%,#8a4a3a 100%)}

/* contact */
.contact-copy{left:145px;top:2460px;width:480px;font-size:20px;line-height:35px;color:var(--ink);font-weight:300}
.follow{left:148px;top:2550px;display:flex;align-items:center;gap:12px;font-size:20px;font-weight:300;color:var(--ink)}
.info-card{left:688px;width:404px;height:116px;border:1.5px solid var(--rule);display:flex;align-items:center;padding-left:40px;gap:20px}
.info-icon{width:66px;height:66px;border-radius:50%;background:var(--gold-soft);display:flex;align-items:center;justify-content:center}
.info-label{font-size:16px;color:var(--ink);text-transform:uppercase}
.info-value{font-size:22px;color:var(--ink)}
.info-value.strong{font-weight:600}

/* footer */
.site-footer{left:0;top:2742px;width:1200px;height:190px;background:var(--footer)}
.footer-brand{left:147px;top:40px;gap:10px}
.footer-brand .brand-mark{width:44px;height:44px}
.footer-brand .nav-font{font-size:34px}
.footer-nav a{position:absolute;top:46px;font-size:21px;text-decoration:none}
.footer-rule{left:130px;top:109px;width:993px;height:2px;background:var(--rule)}
.copyright{left:0;top:148px;width:1200px;text-align:center;font-size:11px;color:var(--muted);text-transform:uppercase}
</style>
</head>
<body>

<header class="abs site-header">
  <div class="abs brand header-brand"><span class="brand-mark"></span><span class="display">LENA MARLOWE</span></div>
</header>

<nav class="abs main-nav nav-font">
  <a class="active" style="left:300px">Home</a>
  <a style="left:444px">About Me</a>
  <a style="left:627px">Gallery</a>
  <a style="left:802px">Contact</a>
  <span class="abs social-dot" style="left:1020px;top:16px;width:34px;height:34px"></span>
</nav>

<section class="abs hero" role="img" aria-label="Close-up of an abstract painting in green, teal and brown brushstrokes">
  <div class="abs hero-arrow" style="left:0">
    <svg width="64" height="74" viewBox="0 0 64 74"><path d="M36 26 L26 37 L36 48" fill="none" stroke="#fff" stroke-width="4"/></svg>
  </div>
  <div class="abs hero-arrow" style="left:1146px;width:54px">
    <svg width="54" height="74" viewBox="0 0 54 74"><path d="M22 26 L32 37 L22 48" fill="none" stroke="#fff" stroke-width="4"/></svg>
  </div>
  <div class="abs hero-title display" style="top:428px;font-size:44px;color:var(--white)">WELCOME TO</div>
  <div class="abs hero-title display" style="top:478px;font-size:66px;color:var(--white)">LENA MARLOWE</div>
  <div class="abs hero-dots"><span></span><span></span><span></span><span></span><span></span><span></span><span></span></div>
</section>

<div class="abs portrait-frame"></div>
<div class="abs portrait" role="img" aria-label="Headshot portrait of the artist"></div>

<h2 class="abs section-heading display" style="left:600px;top:948px">ABOUT ME</h2>
<div class="abs underline" style="left:601px;top:1005px;width:64px"></div>
<div class="abs about-copy">
  <p>Lorem ipsum dolor sit amet, consectetur adipiscing elit, sed do eiusmod tempor incididunt ut labore et dolore magna aliqua. Ut enim ad minim veniam, quis nostrud exercitation</p>
  <p>Duis aute irure dolor in reprehenderit in voluptate velit esse cillum dolore eu fugiat nulla pariatur. Excepteur sint occaecat cupidatat non proident, sunt in culpa qui officia deserunt mollit anim id est laborum.Sed ut perspiciatis unde</p>
</div>
<a class="abs btn-outline nav-font" style="color:var(--gold)">LEARN MORE</a>

<section class="abs gallery">
  <h2 class="abs gallery-title display">PAINTING GALLERY</h2>
  <div class="abs underline" style="left:558px;top:124px;width:64px"></div>
  <svg class="abs" style="left:55px;top:392px" width="32" height="60" viewBox="0 0 32 60"><path d="M28 2 L4 30 L28 58" fill="none" stroke="#222" stroke-width="2"/></svg>
  <div class="abs gallery-artwork" role="img" aria-label="Abstract floral painting in burgundy, blush pink and cream"></div>
  <svg class="abs" style="left:1097px;top:392px" width="32" height="60" viewBox="0 0 32 60"><path d="M4 2 L28 30 L4 58" fill="none" stroke="#222" stroke-width="2"/></svg>
</section>

<h2 class="abs section-heading display" style="left:139px;top:2376px">CONTACT</h2>
<div class="abs underline" style="left:143px;top:2439px;width:92px"></div>
<p class="abs contact-copy">Lorem ipsum dolor sit amet, consectetur adipiscing elit, sed do eiusmod tempor incididunt ut</p>
<div class="abs follow">FOLLOW ME ON <span class="social-dot" style="width:40px;height:40px;display:inline-block"></span></div>

<div class="abs info-card" style="top:2370px">
  <div class="info-icon">
    <svg width="34" height="34" viewBox="0 0 24 24"><path d="M6.6 10.8a15.1 15.1 0 0 0 6.6 6.6l2.2-2.2c.3-.3.7-.4 1-.2 1.1.4 2.3.6 3.6.6.6 0 1 .4 1 1V20c0 .6-.4 1-1 1A17 17 0 0 1 3 4c0-.6.4-1 1-1h3.5c.6 0 1 .4 1 1 0 1.3.2 2.5.6 3.6.1.3 0 .7-.2 1z" fill="#fff"/></svg>
  </div>
  <div><div class="info-label">Phone Number</div><div class="info-value strong">(123) 456 7890</div></div>
</div>
<div class="abs info-card" style="top:2493px">
  <div class="info-icon">
    <svg width="38" height="26" viewBox="0 0 38 26"><rect x="1" y="1" width="36" height="24" fill="none" stroke="#fff" stroke-width="2"/><path d="M1 1 L19 15 L37 1 M1 25 L14 11 M37 25 L24 11" fill="none" stroke="#fff" stroke-width="2"/></svg>
  </div>
  <div><div class="info-label">Email Us</div><div class="info-value">lenamarlowe@info.com</div></div>
</div>

<footer class="abs site-footer">
  <div class="abs brand footer-brand"><span class="brand-mark"></span><span class="nav-font">LENA MARLOWE</span></div>
  <nav class="footer-nav nav-font">
    <a style="left:491px">Home</a>
    <a style="left:596px">About Me</a>
    <a style="left:736px">Gallery</a>
    <a style="left:870px">Contact</a>
  </nav>
  <span class="abs social-dot" style="left:1046px;top:41px;width:34px;height:34px"></span>
  <div class="abs footer-rule"></div>
  <p class="abs copyright">© 2022 Lena Marlowe | All Rights Reserved</p>
</footer>

</body>
</html>
```